Business card for medical clinic

I need an upmarket, modern medical/health business card for my clinic

Contact Information for Business Card

name, address, email, qr code

```html
<!DOCTYPE html>
<html lang="en">
<head>
<meta charset="utf-8">
<title>Meridian Care Clinic – Business Card</title>
<link rel="stylesheet" href="https://fonts.googleapis.com/css2?family=Cinzel:wght@500&family=Arimo:wght@400&display=swap">
<style>
  :root {
    --bg: #1c1c1e;
    --blue-deep: #1d6592;
    --blue-bright: #1897d2;
    --navy: #1d5f8c;
    --ink: #2b2b2b;
    --icon: #1e9ad6;
    --paper: #ffffff;
  }
  * { margin: 0; padding: 0; box-sizing: border-box; }
  html, body { width: 1200px; height: 900px; overflow: hidden; background: var(--bg); }
  .canvas { position: relative; width: 1200px; height: 900px; }

  .card {
    position: absolute; left: 250px; width: 700px; height: 400px;
    border-radius: 22px; overflow: hidden;
  }
  .card--front {
    top: 35px;
    background: linear-gradient(100deg, var(--blue-deep) 0%, #1a80b8 55%, var(--blue-bright) 100%);
  }
  .card--back { top: 465px; background: var(--paper); }

  .wordmark { position: absolute; display: flex; align-items: center; gap: 18px; }
  .wordmark__dot { width: 22px; height: 22px; border-radius: 50%; flex: none; }
  .wordmark__text { font-family: "Cinzel", serif; font-weight: 500; line-height: 1; }
  .wordmark__name { display: block; letter-spacing: 0.02em; }
  .wordmark__sub { display: block; letter-spacing: 0.42em; margin-top: 8px; }

  .card--front .wordmark { left: 50%; top: 50%; transform: translate(-50%, -50%); color: var(--paper); }
  .card--front .wordmark__dot { background: var(--paper); }
  .card--front .wordmark__name { font-size: 46px; }
  .card--front .wordmark__sub { font-size: 19px; text-align: center; }

  .card--back .wordmark { left: 52px; top: 62px; color: var(--navy); }
  .card--back .wordmark__dot { background: var(--navy); width: 16px; height: 16px; }
  .card--back .wordmark__name { font-size: 32px; }
  .card--back .wordmark__sub { font-size: 14px; text-align: center; }

  .holder { position: absolute; right: 44px; top: 118px; text-align: right; }
  .holder__name { font-family: "Cinzel", serif; font-weight: 500; font-size: 30px; color: var(--navy); }
  .holder__role { font-family: "Arimo", sans-serif; font-size: 17px; color: var(--ink); margin-top: 2px; }
  .holder__accent {
    position: absolute; right: 0; top: 96px; width: 22px; height: 40px;
    background: linear-gradient(180deg, var(--navy), var(--blue-bright));
  }

  .contact { position: absolute; left: 52px; top: 216px; font-family: "Arimo", sans-serif; color: var(--ink); }
  .contact__address { font-size: 18px; line-height: 1.35; margin-bottom: 16px; }
  .contact__list { list-style: none; font-size: 18px; }
  .contact__item { display: flex; align-items: center; gap: 10px; margin-bottom: 7px; }
  .contact__icon { width: 16px; height: 16px; flex: none; }
</style>
</head>
<body>
<main class="canvas">

  <section class="card card--front" aria-label="Card front">
    <div class="wordmark">
      <span class="wordmark__dot"></span>
      <span class="wordmark__text">
        <span class="wordmark__name">MERIDIAN CARE</span>
        <span class="wordmark__sub">CLINIC</span>
      </span>
    </div>
  </section>

  <section class="card card--back" aria-label="Card back">
    <div class="wordmark">
      <span class="wordmark__dot"></span>
      <span class="wordmark__text">
        <span class="wordmark__name">MERIDIAN CARE</span>
        <span class="wordmark__sub">CLINIC</span>
      </span>
    </div>

    <span class="holder__accent"></span>
    <div class="holder">
      <p class="holder__name">DANIEL HALE</p>
      <p class="holder__role">Director/Founder</p>
    </div>

    <div class="contact">
      <p class="contact__address">1870 Harbor Lane<br>Westfield AV 30915</p>
      <ul class="contact__list">
        <li class="contact__item">
          <svg class="contact__icon" viewBox="0 0 16 16" aria-hidden="true"><path fill="var(--icon)" d="M3.5 1.5l2.5 0 1 3.5-1.6 1.2a8 8 0 0 0 4.4 4.4L11 9l3.5 1v2.5c0 1-1 2-2 2A11 11 0 0 1 1.5 3.5c0-1 1-2 2-2z"/></svg>
          05310 448 7702
        </li>
        <li class="contact__item">
          <svg class="contact__icon" viewBox="0 0 16 16" aria-hidden="true"><rect x="1" y="3" width="14" height="10" rx="1.5" fill="var(--icon)"/><path d="M1.5 4l6.5 5 6.5-5" fill="none" stroke="#fff" stroke-width="1.3"/></svg>
          hello@meridiancareclinic.com
        </li>
        <li class="contact__item">
          <svg class="contact__icon" viewBox="0 0 16 16" aria-hidden="true"><circle cx="8" cy="8" r="7" fill="var(--icon)"/><path d="M1 8h14M8 1c-3 3.5-3 10.5 0 14M8 1c3 3.5 3 10.5 0 14" fill="none" stroke="#fff" stroke-width="1"/></svg>
          www.meridiancareclinic.com
        </li>
      </ul>
    </div>
  </section>

</main>
</body>
</html>
```